We are a recruitment company based in Norwich/Cambridge England.
I have included our company logo which we want to remain the same.

What we are looking for is a new creative Business card which will really stand out!!

Contact Information for Business Card

Harriet Dunmore
email: Harriet@plavex.co.uk
Address: Brackwell House
Fenmoor Enterprise Park
Partridge Way
Norwich
QB9 3KX
Tel:01632 960418

```html
<!DOCTYPE html>
<html lang="en">
<head>
<meta charset="utf-8">
<title>Plavex Business Card</title>
<link rel="stylesheet" href="https://fonts.googleapis.com/css2?family=Montserrat:wght@500;700&family=Open+Sans:wght@400&display=swap">
<style>
  :root {
    --backdrop: #a4a4a4;
    --card-white: #ffffff;
    --brand-green: #8cc63f;
    --brand-grey: #858589;
    --ink: #2b2b2b;
    --rule: #8d8d8d;
  }
  * { margin: 0; padding: 0; box-sizing: border-box; }
  html, body {
    width: 1200px;
    height: 900px;
    overflow: hidden;
    background: var(--backdrop);
  }
  .stage {
    position: relative;
    width: 1200px;
    height: 900px;
  }
  .card {
    position: absolute;
    top: 170px;
    width: 347px;
    height: 561px;
    text-align: center;
  }
  .card--front { left: 259px; background: var(--card-white); }
  .card--back { left: 632px; background: var(--brand-green); }

  .wordmark {
    position: absolute;
    left: 0;
    right: 0;
    display: flex;
    align-items: center;
    justify-content: center;
    gap: 14px;
    font-family: "Montserrat", sans-serif;
    font-weight: 500;
    font-size: 40px;
    letter-spacing: -0.5px;
  }
  .wordmark__dot {
    width: 44px;
    height: 44px;
    border-radius: 50%;
  }
  .card--front .wordmark { top: 104px; color: var(--brand-green); }
  .card--front .wordmark__dot { background: var(--brand-green); }
  .card--back .wordmark { top: 414px; color: var(--card-white); }
  .card--back .wordmark__dot { background: var(--card-white); }

  .holder {
    position: absolute;
    top: 232px;
    left: 0;
    right: 0;
  }
  .holder__name {
    font-family: "Montserrat", sans-serif;
    font-weight: 700;
    font-size: 19px;
    text-transform: uppercase;
    line-height: 1.1;
  }
  .holder__first { color: var(--brand-green); }
  .holder__last { color: var(--brand-grey); }
  .holder__role {
    font-family: "Open Sans", sans-serif;
    font-size: 14px;
    color: var(--ink);
    margin-top: 2px;
  }

  .contact {
    position: absolute;
    left: 0;
    right: 0;
    font-family: "Open Sans", sans-serif;
    font-size: 14.5px;
    line-height: 20px;
    color: var(--ink);
  }
  .contact--phone { top: 290px; }
  .contact--web { top: 362px; }
  .contact--address { top: 452px; }
  .contact__divider {
    position: relative;
    width: 168px;
    height: 24px;
    margin: 0 auto 6px;
  }
  .contact__divider::before {
    content: "";
    position: absolute;
    left: 0;
    right: 0;
    top: 12px;
    border-top: 1px solid var(--rule);
  }
  .contact__icon {
    position: absolute;
    left: 72px;
    top: 0;
    width: 24px;
    height: 24px;
    border-radius: 50%;
    background: var(--brand-green);
    display: flex;
    align-items: center;
    justify-content: center;
  }

  .site-link {
    position: absolute;
    top: 512px;
    left: 0;
    right: 0;
    font-family: "Open Sans", sans-serif;
    font-size: 14.5px;
    color: var(--card-white);
  }
</style>
</head>
<body>
<main class="stage">

  <section class="card card--front" aria-label="Business card front">
    <div class="wordmark"><span class="wordmark__dot"></span><span>Plavex</span></div>

    <div class="holder">
      <p class="holder__name"><span class="holder__first">Harriet</span> <span class="holder__last">Dunmore</span></p>
      <p class="holder__role">Managing Director</p>
    </div>

    <div class="contact contact--phone">
      <div class="contact__divider">
        <span class="contact__icon">
          <svg width="13" height="13" viewBox="0 0 24 24" aria-hidden="true"><path fill="#fff" d="M6.6 10.8c1.4 2.8 3.8 5.1 6.6 6.6l2.2-2.2c.3-.3.7-.4 1-.2 1.1.4 2.3.6 3.6.6.6 0 1 .4 1 1V20c0 .6-.4 1-1 1C10.6 21 3 13.4 3 4c0-.6.4-1 1-1h3.5c.6 0 1 .4 1 1 0 1.3.2 2.5.6 3.6.1.3 0 .7-.2 1z"/></svg>
        </span>
      </div>
      <p>01632 960418</p>
    </div>

    <div class="contact contact--web">
      <div class="contact__divider">
        <span class="contact__icon">
          <svg width="13" height="13" viewBox="0 0 24 24" aria-hidden="true"><circle cx="12" cy="12" r="9" fill="none" stroke="#fff" stroke-width="2"/><path d="M3 12h18M12 3c3 3 3 15 0 18M12 3c-3 3-3 15 0 18" fill="none" stroke="#fff" stroke-width="1.6"/></svg>
        </span>
      </div>
      <p>Harriet@plavex.co.uk</p>
      <p>www.plavex.co.uk</p>
    </div>

    <div class="contact contact--address">
      <div class="contact__divider">
        <span class="contact__icon">
          <svg width="12" height="14" viewBox="0 0 24 28" aria-hidden="true"><path fill="#fff" d="M12 0C6.5 0 2 4.5 2 10c0 7.5 10 18 10 18s10-10.5 10-18C22 4.5 17.5 0 12 0zm0 14a4 4 0 1 1 0-8 4 4 0 0 1 0 8z"/></svg>
        </span>
      </div>
      <p>Brackwell House, Fenmoor Enterprise Park,</p>
      <p>Partridge Way, Norwich, QB9 3KX</p>
    </div>
  </section>

  <section class="card card--back" aria-label="Business card back">
    <div class="wordmark"><span class="wordmark__dot"></span><span>Plavex</span></div>
    <p class="site-link">www.plavex.co.uk</p>
  </section>

</main>
</body>
</html>
```